GJ & DW Fencing Pty Ltd

We already have an existing logo created by Pixel Harbour however we have restructured to a company. We would like someone to add Pty Ltd to our business name please.

Colors

Designer to choose only greyscale colors for use in the design.

```html
<!DOCTYPE html>
<html lang="en">
<head>
<meta charset="UTF-8">
<title>GJ &amp; DW Fencing Pty Ltd – Business Card</title>
<link href="https://fonts.googleapis.com/css2?family=Merriweather:wght@700;900&family=Lato:wght@400&display=swap" rel="stylesheet">
<style>
  :root {
    --bg: #d9d9d9;
    --ink: #0a0a0a;
    --paper: #ffffff;
    --rule: #8a8a8a;
    --mist-light: #e4e4e4;
    --mist-dark: #c9c9c9;
    --text: #1a1a1a;
  }
  * { margin: 0; padding: 0; box-sizing: border-box; }
  html, body { width: 1200px; height: 900px; overflow: hidden; }
  body {
    background: var(--bg);
    position: relative;
    font-family: "Lato", Arial, sans-serif;
  }
  .card {
    position: absolute;
    width: 520px;
    height: 300px;
    border-radius: 22px;
    overflow: hidden;
    top: 300px;
  }
  .card-front {
    left: 60px;
    background: var(--ink);
    display: flex;
    align-items: center;
    justify-content: center;
  }
  .brand-name {
    font-family: "Merriweather", Georgia, serif;
    font-weight: 900;
    color: var(--paper);
    font-size: 30px;
    letter-spacing: 1px;
    text-align: center;
    line-height: 1.25;
  }
  .card-back {
    left: 620px;
    background: var(--paper);
  }
  .mascot-area {
    position: absolute;
    left: 250px;
    top: 0;
    width: 200px;
    height: 230px;
    border-radius: 45% 45% 30% 30%;
    background: radial-gradient(ellipse at 50% 40%, var(--mist-dark), var(--mist-light) 75%);
  }
  .contact-block {
    position: absolute;
    left: 60px;
    top: 48px;
    width: 300px;
    text-align: center;
    color: var(--text);
  }
  .partner-names {
    font-family: "Merriweather", Georgia, serif;
    font-weight: 700;
    font-size: 15px;
    line-height: 1.5;
    letter-spacing: 0.5px;
  }
  .amp-row {
    display: flex;
    align-items: center;
    justify-content: center;
    gap: 14px;
  }
  .amp-row .rule {
    width: 70px;
    height: 1px;
    background: var(--rule);
  }
  .icons {
    margin-top: 10px;
    display: flex;
    justify-content: center;
    gap: 6px;
  }
  .icon {
    width: 20px;
    height: 20px;
    border-radius: 50%;
    background: var(--ink);
    display: flex;
    align-items: center;
    justify-content: center;
  }
  .phone-row {
    margin-top: 8px;
    display: flex;
    align-items: center;
    justify-content: center;
    gap: 12px;
    font-size: 13px;
  }
  .phone-row .rule {
    width: 55px;
    height: 1px;
    background: var(--rule);
  }
  .email {
    margin-top: 6px;
    font-size: 13px;
  }
  .address-band {
    position: absolute;
    left: 0;
    bottom: 0;
    width: 100%;
    height: 72px;
    background: var(--ink);
    color: var(--paper);
    font-size: 14px;
    display: flex;
    align-items: center;
    justify-content: center;
    padding-right: 40px;
  }
</style>
</head>
<body>
  <section class="card card-front">
    <h1 class="brand-name">GJ &amp; DW FENCING<br>PTY LTD</h1>
  </section>

  <section class="card card-back">
    <div class="mascot-area" role="img" aria-label="Faint grey mascot illustration"></div>
    <div class="contact-block">
      <div class="partner-names">
        <div>GREG JARRETT</div>
        <div class="amp-row"><span class="rule"></span>&amp;<span class="rule"></span></div>
        <div>DANA WALSH</div>
      </div>
      <div class="icons">
        <span class="icon">
          <svg width="12" height="12" viewBox="0 0 24 24"><path fill="#fff" d="M6.6 10.8a15.1 15.1 0 0 0 6.6 6.6l2.2-2.2c.3-.3.7-.4 1-.2 1.1.4 2.3.6 3.6.6.6 0 1 .4 1 1V20c0 .6-.4 1-1 1A17 17 0 0 1 3 4c0-.6.4-1 1-1h3.5c.6 0 1 .4 1 1 0 1.3.2 2.5.6 3.6.1.3 0 .7-.2 1z"/></svg>
        </span>
        <span class="icon">
          <svg width="12" height="12" viewBox="0 0 24 24"><path fill="#fff" d="M3 5h18v14H3z"/><path d="M3 5l9 7 9-7" fill="none" stroke="#0a0a0a" stroke-width="2"/></svg>
        </span>
      </div>
      <div class="phone-row"><span class="rule"></span>044 5219370<span class="rule"></span></div>
      <div class="email">Gjdwfencing@mailbox.com</div>
    </div>
    <div class="address-band">PO Box 418 Harlow WA 6350</div>
  </section>
</body>
</html>
```